Brightcoat Painting Services Requires a New Responsive Site

Hi Designers,

Our current website is this www.brightcoatpainting.com.au for some idea.
I made it on Adobe Muse, its very basic.
I would like it to be redesigned to look more professional and also responsive. I actually know how to do html5 and css but I think others will do this much better than me.

I do not need content because I am a copywriter and would like to do all SEO and copy myself.

The most improtant things to remember is that the site cannot use a CMS
and the code needs to be understandable so that I can go in and add content later on and do SEO work.

Also the site requires an additional testimonial page. I would imagine a nice gallery would be a great addition too(something that I can add images too through html. Also in it is important for it to contain those brand images on the front page as it increases authority. I will attach them onto the brief.

Those two files of nearbyfind and tradeleafs are local directories where we have reviews so a placement of those on the testimonail page would make great sense. I will to the href myself.

Anyway, good luck!

I look forward to see your designs :D
Updates

I have just been informed that on this site websites are simply designed and not built (developed) if this is the case please stop working on your designs and spending more time on this project. I REQUIRE DEVELOPMENT ALSO AND HAVE ALREADY CONTACTED SUPPORT.

Target Market(s)

The target market is 30-75 high income earners.

Industry/Entity Type

Painting

Number of Pages Required

5+ page

Font styles to use
Serif
Sans Serif

Requirements
Must have
• attractive gallery, and the brand icons uploaded.
• must be responsive
• web carousel (with the different types of work we do). eg domestic, commercial, industrial etc.
Nice to have
• a little interactivity
• corporate a natural design that goes well with our logo
Should not have
• any content. just write jiberish to fill in the spaces.
• I will be doing all copy and SEO myself.
• More than five pages, bascially the four that already exist plus the testimonail one.

```html
<!DOCTYPE html>
<html lang="en">
<head>
<meta charset="utf-8">
<title>Brightcoat Painting</title>
<link href="https://fonts.googleapis.com/css2?family=Libre+Baskerville:wght@400;700&family=Open+Sans:wght@400;600;700&display=swap" rel="stylesheet">
<style>
:root{
  --brand:#3b7594;
  --brand-dark:#2f6482;
  --ink:#333;
  --muted:#555;
  --footer-bar:#1e2a33;
  --band-top:#b9b9b9;
  --band-bottom:#f2f2f2;
  --frame:#dcdcdc;
  --placeholder:#d6d9dc;
  --white:#fff;
}
*{box-sizing:border-box;margin:0;padding:0}
html,body{width:1200px;height:2456px;overflow:hidden}
body{position:relative;background:var(--white);font-family:"Open Sans",Arial,sans-serif;color:var(--ink)}
.abs{position:absolute}

.topbar{left:0;top:0;width:1200px;height:41px;background:var(--brand);color:var(--white);font-size:13px}
.topbar .contact{top:12px;display:flex;align-items:center;gap:10px}
.social{display:flex;gap:6px}
.social span{width:22px;height:22px;border-radius:50%;background:var(--white);display:block}
.topbar .social{right:131px;top:9px}

.logo-mark{background:linear-gradient(160deg,#3d86a8 0%,#7d8c96 50%,#3f4a52 100%)}
.logo-name{font-family:"Libre Baskerville",Georgia,serif;font-weight:700;font-size:13px;color:#2b3a44;letter-spacing:.5px}
.search{left:876px;top:77px;width:192px;height:25px;border:1px solid #ccc;display:flex}
.search span{flex:1;font-size:11px;color:#aaa;padding:5px 8px}
.search i{width:26px;background:var(--brand);display:flex;align-items:center;justify-content:center}
.nav{top:131px;left:574px;display:flex;font-size:12px;text-transform:uppercase}
.nav a{display:block;height:28px;line-height:28px;color:#222;text-decoration:none;padding:0 13px}
.nav a.active{background:var(--brand);color:var(--white)}

.hero{left:0;top:198px;width:1200px;height:563px;background:linear-gradient(180deg,#e8e4de 0%,#9a5e3a 35%,#7a4a2e 65%,#5a3d2c 100%)}
.hero-caption{left:0;top:638px;width:1200px;height:123px;background:rgba(40,40,40,.55);color:var(--white)}
.hero-caption h1{position:absolute;left:147px;top:26px;font-family:"Libre Baskerville",Georgia,serif;font-weight:400;font-size:35px}
.hero-caption p{position:absolute;left:147px;top:79px;font-size:14px}
.arrow{top:680px}

.welcome h2{left:0;width:1200px;top:805px;text-align:center;font-family:"Libre Baskerville",Georgia,serif;font-weight:400;font-size:18px;color:#222;text-transform:uppercase}
.welcome h2 b{color:var(--brand);font-weight:400;margin-left:8px}
.welcome p{left:205px;width:790px;top:850px;text-align:center;font-size:12.5px;line-height:28px;color:var(--muted)}

.band{left:0;width:1200px;background:linear-gradient(180deg,var(--band-top) 0%,var(--band-bottom) 100%)}
.section-title{font-family:"Libre Baskerville",Georgia,serif;font-weight:400;font-size:18px;color:var(--brand);text-transform:uppercase}
.band .section-title{position:absolute;left:0;width:1200px;text-align:center}

.service{top:1053px;width:223px;height:238px;background:var(--white);text-align:center;box-shadow:0 14px 14px -10px rgba(0,0,0,.35)}
.service .icon{width:86px;height:80px;margin:20px auto 0;border-radius:14px}
.service h3{font-size:13px;font-weight:400;text-transform:uppercase;margin-top:14px;color:#222}
.service p{font-size:12px;line-height:24px;color:var(--muted);padding:6px 16px 0}

.photo{width:297px;height:189px;background:var(--frame);padding:10px}
.photo div{width:100%;height:100%}

.client{top:1956px;width:172px;height:128px;background:var(--white);display:flex;align-items:center;justify-content:center;gap:8px;font-size:16px;font-weight:700;color:#222}
.client .dot{width:16px;height:16px;background:var(--brand);border-radius:50%}
.client .placeholder{width:84px;height:84px;background:var(--placeholder)}

.footer{left:0;top:2130px;width:1200px;height:281px;background:var(--brand);color:var(--white)}
.footer h4{position:absolute;top:52px;font-family:"Libre Baskerville",Georgia,serif;font-weight:400;font-size:16px;text-transform:uppercase}
.footer p{font-size:12px;line-height:22px}
.post{position:absolute;display:flex;gap:12px}
.post .thumb{width:95px;height:75px;background:linear-gradient(135deg,#e9e5df,#8d7a6a)}
.post p{width:120px}
.post .comment{display:flex;align-items:center;gap:8px}
.field{position:absolute;width:210px;height:26px;background:var(--white);color:#777;font-size:11px;padding:5px 8px}
.submit{position:absolute;top:217px;width:66px;height:26px;background:#555;font-size:12px;line-height:26px;text-align:center}

.bottombar{left:0;top:2411px;width:1200px;height:45px;background:var(--footer-bar);color:var(--white);font-size:12px}
</style>
</head>
<body>

<header>
  <div class="abs topbar">
    <div class="abs contact" style="left:137px">
      <svg width="13" height="10" viewBox="0 0 13 10"><rect x=".5" y=".5" width="12" height="9" fill="none" stroke="#fff"/><path d="M.5 .5l6 5 6-5" fill="none" stroke="#fff"/></svg>
      hello@brightcoatmail.com
    </div>
    <div class="abs contact" style="left:354px">
      <svg width="13" height="13" viewBox="0 0 24 24"><path fill="#fff" d="M6.6 10.8a15 15 0 006.6 6.6l2.2-2.2c.3-.3.7-.4 1-.2 1.1.4 2.3.6 3.6.6.6 0 1 .4 1 1V20c0 .6-.4 1-1 1A17 17 0 013 4c0-.6.4-1 1-1h3.5c.6 0 1 .4 1 1 0 1.3.2 2.5.6 3.6.1.3 0 .7-.2 1z"/></svg>
      (100) 555-0142
    </div>
    <div class="abs social" aria-label="Social links"><span></span><span></span><span></span><span></span><span></span></div>
  </div>

  <div class="abs logo-mark" style="left:152px;top:54px;width:118px;height:100px" role="img" aria-label="Brightcoat Painting house logo"></div>
  <div class="abs logo-name" style="left:131px;top:162px">BRIGHTCOAT PAINTING</div>

  <div class="abs search"><span>Search</span><i><svg width="12" height="12" viewBox="0 0 12 12"><circle cx="5" cy="5" r="3.5" fill="none" stroke="#fff" stroke-width="1.6"/><path d="M7.6 7.6L11 11" stroke="#fff" stroke-width="1.6"/></svg></i></div>

  <nav class="abs nav">
    <a class="active" href="#">Home</a><a href="#" style="margin-left:20px">Services</a><a href="#" style="margin-left:24px">Gallery</a><a href="#" style="margin-left:24px">About Us</a><a href="#" style="margin-left:24px">Contact Us</a>
  </nav>
</header>

<section>
  <div class="abs hero" role="img" aria-label="Living room with brown painted walls, white fireplace and large windows"></div>
  <div class="abs hero-caption">
    <h1>Domestic and commercial painting services</h1>
    <p>Lorem Ipsum is simply text of the printing and typesetting industry. Lorem Ipsum has been the industry's .</p>
  </div>
  <svg class="abs arrow" style="left:62px" width="20" height="30" viewBox="0 0 20 30"><path d="M15 4L5 15l10 11" fill="none" stroke="#fff" stroke-width="2.5"/></svg>
  <svg class="abs arrow" style="left:1118px" width="20" height="30" viewBox="0 0 20 30"><path d="M5 4l10 11L5 26" fill="none" stroke="#fff" stroke-width="2.5"/></svg>
</section>

<section class="welcome">
  <h2 class="abs">Welcome to<b>Brightcoat Painting</b></h2>
  <p class="abs">As the industry leaders in file management software systems for over a decade, Claimwise Online has been providing secure online claims software to a broad range of clients worldwide. The first part of providing any technical assistance to a company is to ensure that you understand what they do in their day to day business. It's a complete file management system.</p>
</section>

<section class="abs band" style="top:961px;height:376px">
  <h2 class="section-title" style="top:30px">Our Services</h2>
</section>
<div class="abs service" style="left:133px"><div class="icon" style="background:linear-gradient(135deg,#f2c24a,#d8632e)" role="img" aria-label="Paint palette icon"></div><h3>Domestic Painting</h3><p>Our management consulting services address our clienteles' crucial issues</p></div>
<div class="abs service" style="left:368px"><div class="icon" style="background:linear-gradient(135deg,#f6d9a0,#d39445)" role="img" aria-label="Easel icon"></div><h3>Commercial Painting</h3><p>Internal controls, including an organization's procedures and policies</p></div>
<div class="abs service" style="left:606px"><div class="icon" style="background:linear-gradient(135deg,#8a8f95,#3e4348)" role="img" aria-label="Tool folder icon"></div><h3>Industrial Painting</h3><p>Our team of highly experienced and proficient legal team is ready to offer a range</p></div>
<div class="abs service" style="left:843px"><div class="icon" style="background:linear-gradient(135deg,#6bb8e0,#2f75b0)" role="img" aria-label="Brushes and pencils icon"></div><h3>Heritage Painting</h3><p>Investments are complex and intricate in nature, and for this they require</p></div>

<section>
  <h2 class="abs section-title" style="left:134px;top:1387px">Latest Photo Gallery</h2>
  <div class="abs photo" style="left:133px;top:1434px"><div style="background:linear-gradient(180deg,#4f86c4 0%,#8fa9c0 45%,#7b5a44 70%,#4c6a3a 100%)" role="img" aria-label="Brick commercial building with hedge"></div></div>
  <div class="abs photo" style="left:452px;top:1434px"><div style="background:linear-gradient(180deg,#3a7fd0 0%,#a8c3e0 40%,#b9b9b9 70%,#7a8a6a 100%)" role="img" aria-label="Large grey weatherboard house"></div></div>
  <div class="abs photo" style="left:771px;top:1434px"><div style="background:linear-gradient(180deg,#3d8fe0 0%,#c98a74 45%,#c46a55 65%,#4f8f3a 100%)" role="img" aria-label="Salmon coloured villa with red roof"></div></div>
  <div class="abs photo" style="left:133px;top:1648px"><div style="background:linear-gradient(180deg,#4a8ad6 0%,#cfd4d8 45%,#7d8f6a 70%,#9a9a9a 100%)" role="img" aria-label="Office building with palm trees and sign"></div></div>
  <div class="abs photo" style="left:452px;top:1648px"><div style="background:linear-gradient(180deg,#1f5fb0 0%,#c86a2a 40%,#b8a88a 65%,#3e6e2e 100%)" role="img" aria-label="Two storey house with autumn tree"></div></div>
  <div class="abs photo" style="left:771px;top:1648px"><div style="background:linear-gradient(90deg,#8a3a2a 0%,#a24a36 50%,#4f7a3a 80%,#6e8f4e 100%)" role="img" aria-label="Red brick school building with cross"></div></div>
</section>

<section class="abs band" style="top:1887px;height:243px">
  <h2 class="section-title" style="top:30px">Our Clients</h2>
</section>
<div class="abs client" style="left:131px"><span class="dot"></span>tradeleafs</div>
<div class="abs client" style="left:322px">Tallmark Paints</div>
<div class="abs client" style="left:514px">Duravel</div>
<div class="abs client" style="left:704px"><span class="dot"></span>nearbyfind</div>
<div class="abs client" style="left:897px"><div class="placeholder" role="img" aria-label="Workmanship warranty badge"></div></div>

<footer class="abs footer">
  <div class="abs logo-mark" style="left:131px;top:44px;width:108px;height:84px" role="img" aria-label="Brightcoat Painting house logo"></div>
  <div class="abs logo-name" style="left:131px;top:145px;color:#fff;font-size:12px">BRIGHTCOAT PAINTING</div>
  <p class="abs" style="left:131px;top:171px;width:215px">Lorem Ipsum is simply dummy text of the printing and typesetting industry.</p>

  <h4 style="left:383px">Recent Posts</h4>
  <div class="post" style="left:385px;top:86px"><div class="thumb" role="img" aria-label="Bright living room interior"></div><p>Comincia a vendere vostri articoli propri,<span class="comment"><svg width="12" height="11" viewBox="0 0 12 11"><path d="M1 1h10v7H5l-3 2.5V8H1z" fill="#fff"/></svg>1 comment</span></p></div>
  <div class="post" style="left:385px;top:175px"><div class="thumb" role="img" aria-label="Furnished lounge interior"></div><p>Comincia a vendere vostri articoli propri,<span class="comment"><svg width="12" height="11" viewBox="0 0 12 11"><path d="M1 1h10v7H5l-3 2.5V8H1z" fill="#fff"/></svg>1 comment</span></p></div>

  <h4 style="left:660px">Contacts</h4>
  <p class="abs" style="left:660px;top:88px;font-size:11px;line-height:20px">12/48 Harlow Road<br>Elmsford,<br>SA, 5071</p>
  <p class="abs" style="left:660px;top:153px;line-height:26px"><b>Phone</b><br>08 7010 2200<br>08 7010 3344</p>

  <h4 style="left:863px">Newsletter</h4>
  <p class="abs" style="left:863px;top:85px;width:225px;font-size:11.5px">Sign up for our newsletter and get the latest news.</p>
  <div class="field" style="left:863px;top:139px">Name</div>
  <div class="field" style="left:863px;top:178px">Email</div>
  <div class="submit" style="left:863px">Submit</div>
</footer>

<div class="abs bottombar">
  <span class="abs" style="left:131px;top:14px">© 2014 &nbsp;Brightcoat painting. All rights reserved</span>
  <div class="abs social" style="left:906px;top:11px" aria-label="Social links"><span></span><span></span><span></span><span></span><span></span></div>
</div>

</body>
</html>
```